Australian Trucking Company Requires Professional Looking Stationary

We require a professional looking stationary design that incorporates our newly designed logo.

Our business, called "Brell Haulage Contracting", provides contracting work, transport and logistics to business in Western Australia particularly with links to the mining sector.

We are a small business looking to expand and our new logo and our new stationary will help develop our brand image in our market place.

Target Market(s)

Businesses and Corporation with links to the Mining Sector

Industry/Entity Type

Small Business

Requirements
Must have
• The letterhead must have the following details:
The new logo

Text saying: "Brell Holdings Pty Ltd (ACN 582 316 907) ATF The Brell Discretionary Trust T/AS"
"ABN 71 834 209 553"
Address "P.O Box 817 Wattlegrove WA, 6958"
Phone: 08 9352 7140
Email: brellhaul@mailbox-example.com.au

The text on the letterhead should be editable as the details are likely to change in the near future. Provision should be made for a website address all though one isn't available at the moment.

The styling, layout and font text is entirely up to the designer.

```html
<!DOCTYPE html>
<html lang="en">
<head>
<meta charset="utf-8">
<title>Brell Haulage Contracting – Stationery</title>
<link rel="stylesheet" href="https://fonts.googleapis.com/css2?family=Open+Sans:wght@400;600;700&display=swap">
<style>
  :root {
    --backdrop: #e9e6e1;
    --paper: #ffffff;
    --brand-red: #a3121c;
    --deep-red: #6e0a10;
    --bright-red: #d71a22;
    --silver: #c9c9c9;
    --ink: #222222;
    --rule: #555555;
    --mark-grey: #8a8a8a;
    --edge: #d4d4d4;
  }
  * { box-sizing: border-box; margin: 0; padding: 0; }
  html, body { width: 1200px; height: 789px; overflow: hidden; background: var(--backdrop); }
  body { font-family: "Open Sans", Arial, sans-serif; color: var(--ink); }
  .stage { position: relative; width: 1200px; height: 789px; overflow: hidden; }

  .sheet { position: absolute; background: var(--paper); box-shadow: 0 1px 4px rgba(0,0,0,.18); overflow: hidden; }
  .wave { position: absolute; left: 0; bottom: 0; width: 100%; display: block; }

  /* brand lockup */
  .brand { position: absolute; display: flex; align-items: center; gap: 8px; }
  .brand-square { width: 30px; height: 30px; background: var(--mark-grey); }
  .brand-name { color: var(--brand-red); font-weight: 700; text-transform: uppercase; line-height: 1.02; letter-spacing: .3px; }

  /* fax sheet */
  .fax { left: 23px; top: 73px; width: 455px; height: 641px; }
  .fax .brand { left: 120px; top: 20px; }
  .fax .brand-square { width: 44px; height: 44px; }
  .fax .brand-name { font-size: 15px; }
  .fax-entity { position: absolute; top: 80px; left: 0; width: 100%; text-align: center; font-size: 7.4px; color: var(--brand-red); }
  .fax-title { position: absolute; left: 30px; top: 180px; font-size: 26px; font-weight: 400; letter-spacing: .5px; }
  .fax-fields { position: absolute; left: 30px; top: 228px; width: 395px; display: grid; grid-template-columns: 235px 160px; row-gap: 10px; }
  .field { font-size: 7px; border-bottom: 1px solid var(--rule); height: 14px; padding-top: 2px; }
  .fax-options { position: absolute; left: 30px; top: 346px; width: 395px; display: flex; justify-content: space-between; font-size: 7.4px; }
  .option { display: flex; align-items: center; gap: 6px; }
  .option::before { content: ""; width: 9px; height: 9px; border: 1px solid var(--rule); }
  .fax-contact { position: absolute; right: 16px; bottom: 18px; text-align: right; color: #fff; font-size: 7.6px; line-height: 11.6px; }
  .fax-contact .abn { margin-bottom: 9px; }
  .contact-line { display: flex; justify-content: flex-end; align-items: center; gap: 6px; }
  .contact-line svg { width: 7px; height: 7px; fill: #fff; }
  .sheet-label { position: absolute; left: 216px; top: 720px; font-size: 14px; color: #fff; text-shadow: 0 0 2px rgba(0,0,0,.35); }

  /* red-flap envelope */
  .envelope-red { left: 627px; top: 44px; width: 520px; height: 232px; }
  .envelope-red .flap { position: absolute; left: 0; top: 0; width: 100%; height: 95px; }
  .flap-name { position: absolute; left: 0; top: 38px; width: 100%; text-align: center; color: rgba(255,255,255,.55); font-weight: 700; font-size: 10px; text-transform: uppercase; }

  /* window-flap envelope */
  .envelope-wave { left: 513px; top: 145px; width: 520px; height: 348px; }
  .envelope-wave .flap { position: absolute; left: 0; top: 0; width: 100%; height: 117px; }
  .flap-mark { position: absolute; left: 244px; top: 36px; width: 34px; height: 34px; background: var(--mark-grey); }
  .envelope-wave .brand { left: 20px; top: 128px; }
  .envelope-wave .brand-name { font-size: 12.5px; }
  .envelope-address { position: absolute; font-size: 8.4px; color: var(--brand-red); }
  .envelope-wave .envelope-address { left: 41px; top: 180px; }
  .envelope-web { position: absolute; font-size: 8px; }
  .envelope-wave .envelope-web { right: 10px; bottom: 13px; color: #fff; display: flex; align-items: center; gap: 6px; }

  /* plain envelope */
  .envelope-plain { left: 513px; top: 523px; width: 520px; height: 231px; }
  .envelope-plain .brand { left: 14px; top: 14px; }
  .envelope-plain .brand-name { font-size: 12.5px; }
  .envelope-plain .envelope-address { left: 40px; top: 69px; }
  .envelope-plain .envelope-web { left: 58px; bottom: 8px; color: var(--brand-red); }

  /* business card */
  .card { left: 1063px; top: 407px; width: 150px; height: 173px; border-radius: 12px; }
  .card .brand { left: 12px; top: 16px; gap: 6px; }
  .card .brand-square { width: 28px; height: 28px; }
  .card .brand-name { font-size: 13px; }
  .card-name { position: absolute; left: 23px; top: 102px; font-size: 11.5px; font-weight: 700; color: var(--brand-red); }
  .card-title { position: absolute; left: 23px; top: 117px; font-size: 9.5px; color: var(--brand-red); letter-spacing: .8px; }
</style>
</head>
<body>
<main class="stage">

  <!-- Fax sheet -->
  <section class="sheet fax">
    <div class="brand">
      <div class="brand-square"></div>
      <div class="brand-name">Brell<br>Haulage<br>Contracting</div>
    </div>
    <p class="fax-entity">Brell Holdings Pty Ltd (ACN 582 316 907) ATF The Brell Discretionary Trust T/AS</p>
    <h1 class="fax-title">FAX</h1>
    <div class="fax-fields">
      <div class="field">To :</div><div class="field">From :</div>
      <div class="field">Fax :</div><div class="field">Pages :</div>
      <div class="field">Phone :</div><div class="field">Date :</div>
      <div class="field">Re :</div><div class="field">CC :</div>
    </div>
    <div class="fax-options">
      <span class="option">Urgent</span>
      <span class="option">For Review</span>
      <span class="option">Please Comment</span>
      <span class="option">Please Reply</span>
      <span class="option">Please Recycle</span>
    </div>
    <svg class="wave" viewBox="0 0 455 112" height="112" preserveAspectRatio="none">
      <defs>
        <linearGradient id="faxRed" x1="0" y1="0" x2="1" y2="0">
          <stop offset="0" stop-color="#b5161f"/><stop offset="1" stop-color="#6e0a10"/>
        </linearGradient>
      </defs>
      <path d="M0,78 C140,76 300,8 455,2 L455,112 L0,112 Z" fill="#1b1b1b"/>
      <path d="M0,84 C140,82 300,14 455,9 L455,112 L0,112 Z" fill="#d9d9d9"/>
      <path d="M0,90 C140,88 300,22 455,16 L455,112 L0,112 Z" fill="url(#faxRed)"/>
      <path d="M0,94 C120,92 200,104 300,112 L0,112 Z" fill="#fff" opacity=".92"/>
    </svg>
    <div class="fax-contact">
      <div class="abn">ABN 71 834 209 553</div>
      <div class="contact-line">08 9352 7140 <svg viewBox="0 0 10 10"><path d="M2 1h2l1 2.5-1.2 1a5 5 0 0 0 2 2l1-1.2L9 6.5v2A1 1 0 0 1 8 9.5 7.5 7.5 0 0 1 .5 2 1 1 0 0 1 2 1z"/></svg></div>
      <div class="contact-line">brellhaul@mailbox-example.com.au <svg viewBox="0 0 10 10"><rect x="0" y="2" width="10" height="6"/></svg></div>
      <div class="contact-line">www.brellhaulage-example.com.au <svg viewBox="0 0 10 10"><circle cx="5" cy="5" r="4.5"/></svg></div>
      <div class="contact-line">P.O Box 817 Wattlegrove WA, 6958 <svg viewBox="0 0 10 10"><path d="M5 0 10 5H8.5v5h-7V5H0z"/></svg></div>
    </div>
  </section>
  <p class="sheet-label">Option 3</p>

  <!-- Envelope back with red flap -->
  <section class="sheet envelope-red">
    <svg class="flap" viewBox="0 0 520 95" preserveAspectRatio="none">
      <defs>
        <linearGradient id="flapRed" x1="0" y1="0" x2="0" y2="1">
          <stop offset="0" stop-color="#d71a22"/><stop offset="1" stop-color="#a3121c"/>
        </linearGradient>
      </defs>
      <path d="M0,0 H520 C515,30 500,32 470,40 L275,90 Q260,95 245,90 L50,40 C20,32 5,30 0,0 Z" fill="url(#flapRed)"/>
    </svg>
    <p class="flap-name">Brell Haulage Contracting</p>
  </section>

  <!-- Envelope with flap and wave -->
  <section class="sheet envelope-wave">
    <svg class="flap" viewBox="0 0 520 117" preserveAspectRatio="none">
      <path d="M0,0 C6,30 20,36 50,44 L245,92 Q260,96 275,92 L470,44 C500,36 514,30 520,0" fill="none" stroke="#bdbdbd" stroke-width="1"/>
      <line x1="0" y1="116.5" x2="520" y2="116.5" stroke="#e2e2e2" stroke-width="1"/>
    </svg>
    <div class="flap-mark"></div>
    <div class="brand">
      <div class="brand-square"></div>
      <div class="brand-name">Brell<br>Haulage<br>Contracting</div>
    </div>
    <p class="envelope-address">P.O Box 817 Wattlegrove WA, 6958</p>
    <svg class="wave" viewBox="0 0 520 104" height="104" preserveAspectRatio="none">
      <defs>
        <linearGradient id="envRed" x1="0" y1="0" x2="1" y2="0">
          <stop offset="0" stop-color="#b5161f"/><stop offset="1" stop-color="#6e0a10"/>
        </linearGradient>
      </defs>
      <path d="M0,74 C170,72 340,8 520,0 L520,104 L0,104 Z" fill="#1b1b1b"/>
      <path d="M0,79 C170,77 340,13 520,6 L520,104 L0,104 Z" fill="#d9d9d9"/>
      <path d="M0,84 C170,82 340,20 520,13 L520,104 L0,104 Z" fill="url(#envRed)"/>
    </svg>
    <p class="envelope-web">www.brellhaulage-example.com.au
      <svg width="7" height="7" viewBox="0 0 10 10"><circle cx="5" cy="5" r="4.5" fill="#fff"/></svg></p>
  </section>

  <!-- Plain envelope -->
  <section class="sheet envelope-plain">
    <div class="brand">
      <div class="brand-square"></div>
      <div class="brand-name">Brell<br>Haulage<br>Contracting</div>
    </div>
    <p class="envelope-address">P.O Box 817 Wattlegrove WA, 6958</p>
    <p class="envelope-web">www.brellhaulage-example.com.au</p>
  </section>

  <!-- Business card -->
  <section class="sheet card">
    <div class="brand">
      <div class="brand-square"></div>
      <div class="brand-name">Brell<br>Haulage<br>Contr.</div>
    </div>
    <p class="card-name">Your Name</p>
    <p class="card-title">Title</p>
    <svg class="wave" viewBox="0 0 150 50" height="50" preserveAspectRatio="none">
      <path d="M0,30 C50,28 100,8 150,2 L150,50 L0,50 Z" fill="#1b1b1b"/>
      <path d="M0,34 C50,32 100,12 150,6 L150,50 L0,50 Z" fill="#d9d9d9"/>
      <path d="M0,38 C50,36 100,16 150,11 L150,50 L0,50 Z" fill="#a3121c"/>
      <path d="M0,41 C40,41 80,46 110,50 L0,50 Z" fill="#fff"/>
    </svg>
  </section>

</main>
</body>
</html>
```